Dental Medical History Form - Content provided

Design a medical history form for a dental practice. Content is provided so all that is needed is the formatting to make it look great and easy to read.

"Patient Information" to include all information contained in top portion of the "Patient Medical History Form" docx file.

"Medical History" should follow the formatting and content of the "Exact Medical History" file as this is what the entry fields look like in our practice software and so we would like it to match.

1st page - Patient info, allergies, medications, antibiotics, joint replacement, pregnancy.

2nd page - Do you have, or have you had, any of the following? . . . . . . .
Updates

Target Market(s)

All ages but must be clear enough for elderly to read. Use as much space as possible to keep font size bigger yet keep to two pages

Industry/Entity Type

Dental

Font styles to use
Sans Serif

Requirements
Must have
• All content provided
• Our logo at the top (file provided)
• Century Gothic Font
• Limit to two pages

```html
<!DOCTYPE html>
<html lang="en">
<head>
<meta charset="utf-8">
<title>Medical History Form – Page 2</title>
<link rel="stylesheet" href="https://fonts.googleapis.com/css2?family=PT+Sans+Narrow:wght@400;700&display=swap">
<style>
  :root {
    --backdrop: #e9e8e6;
    --paper: #ffffff;
    --ink: #3a3a3a;
    --ink-soft: #5a5a5a;
    --box: #e6e3df;
    --box-edge: #cfcac4;
    --spine: #d8d3cd;
    --rule: #8a8682;
  }
  * { box-sizing: border-box; margin: 0; padding: 0; }
  html, body { width: 1200px; height: 784px; overflow: hidden; }
  body {
    background: var(--backdrop);
    font-family: "PT Sans Narrow", "Arial Narrow", sans-serif;
    color: var(--ink);
    display: flex; align-items: center; justify-content: center;
  }
  .form-page {
    width: 560px; height: 760px;
    background: var(--paper);
    border-top: 8px solid var(--spine);
    box-shadow: 0 2px 6px rgba(0,0,0,.12);
    padding: 14px 30px 16px 34px;
    display: flex; flex-direction: column;
  }
  .form-title {
    font-weight: 700; font-size: 15px; text-align: right;
    margin-bottom: 10px; color: var(--ink);
  }
  .history-columns { display: grid; grid-template-columns: 1fr 1fr; column-gap: 26px; flex: 1; }
  .condition-list { list-style: none; }
  .condition, .group-title {
    height: 16.2px; line-height: 16.2px; font-size: 11.5px;
    display: flex; align-items: center;
  }
  .group-title { font-weight: 700; font-size: 12.5px; }
  .condition-name { flex: 1; white-space: nowrap; overflow: hidden; color: var(--ink-soft); }
  .answer { display: flex; align-items: center; gap: 4px; font-size: 10.5px; color: var(--ink-soft); margin-left: 6px; }
  .answer span { width: 14px; text-align: right; }
  .tick-box { width: 11px; height: 11px; background: var(--box); border: 1px solid var(--box-edge); }
  .sign-off { margin-top: 8px; }
  .sign-lines { display: flex; gap: 40px; margin-bottom: 8px; }
  .sign-field { display: flex; align-items: flex-end; gap: 8px; font-weight: 700; font-size: 13px; }
  .sign-field.date { flex: 0 0 170px; }
  .sign-field.signature { flex: 1; }
  .sign-line { flex: 1; border-bottom: 1px solid var(--rule); height: 14px; }
  .thanks { font-size: 9px; text-align: center; color: var(--ink-soft); line-height: 1.35; }
</style>
</head>
<body>
<main class="form-page">
  <h1 class="form-title">Do you have, or have you had, any of the following?</h1>
  <div class="history-columns">
    <ul class="condition-list">
      <li class="group-title">Dental</li>
      <li class="condition"><span class="condition-name">Acid Reflux</span><span class="answer"><span>Yes</span><i class="tick-box"></i><span>No</span><i class="tick-box"></i></span></li>
      <li class="condition"><span class="condition-name">Bad Breath/Taste</span><span class="answer"><span>Yes</span><i class="tick-box"></i><span>No</span><i class="tick-box"></i></span></li>
      <li class="condition"><span class="condition-name">Bleeding/Swollen/Sore Gums</span><span class="answer"><span>Yes</span><i class="tick-box"></i><span>No</span><i class="tick-box"></i></span></li>
      <li class="condition"><span class="condition-name">Blisters/Ulcers in Mouth</span><span class="answer"><span>Yes</span><i class="tick-box"></i><span>No</span><i class="tick-box"></i></span></li>
      <li class="condition"><span class="condition-name">Broken tooth/filling</span><span class="answer"><span>Yes</span><i class="tick-box"></i><span>No</span><i class="tick-box"></i></span></li>
      <li class="condition"><span class="condition-name">Burning tongue</span><span class="answer"><span>Yes</span><i class="tick-box"></i><span>No</span><i class="tick-box"></i></span></li>
      <li class="condition"><span class="condition-name">Dry mouth</span><span class="answer"><span>Yes</span><i class="tick-box"></i><span>No</span><i class="tick-box"></i></span></li>
      <li class="condition"><span class="condition-name">Food collection between teeth</span><span class="answer"><span>Yes</span><i class="tick-box"></i><span>No</span><i class="tick-box"></i></span></li>
      <li class="condition"><span class="condition-name">Grinding/clenching teeth (day/night)</span><span class="answer"><span>Yes</span><i class="tick-box"></i><span>No</span><i class="tick-box"></i></span></li>
      <li class="condition"><span class="condition-name">Loose teeth</span><span class="answer"><span>Yes</span><i class="tick-box"></i><span>No</span><i class="tick-box"></i></span></li>
      <li class="condition"><span class="condition-name">Crooked teeth</span><span class="answer"><span>Yes</span><i class="tick-box"></i><span>No</span><i class="tick-box"></i></span></li>
      <li class="condition"><span class="condition-name">Discoloured teeth</span><span class="answer"><span>Yes</span><i class="tick-box"></i><span>No</span><i class="tick-box"></i></span></li>
      <li class="condition"><span class="condition-name">Sensitivity to Hot/Cold</span><span class="answer"><span>Yes</span><i class="tick-box"></i><span>No</span><i class="tick-box"></i></span></li>
      <li class="condition"><span class="condition-name">Tooth pain when chewing</span><span class="answer"><span>Yes</span><i class="tick-box"></i><span>No</span><i class="tick-box"></i></span></li>
      <li class="condition"><span class="condition-name">Jaw pain/Fracture</span><span class="answer"><span>Yes</span><i class="tick-box"></i><span>No</span><i class="tick-box"></i></span></li>
      <li class="condition"><span class="condition-name">Orthodontic treatment/history</span><span class="answer"><span>Yes</span><i class="tick-box"></i><span>No</span><i class="tick-box"></i></span></li>
      <li class="condition"><span class="condition-name">Oral Cancer</span><span class="answer"><span>Yes</span><i class="tick-box"></i><span>No</span><i class="tick-box"></i></span></li>
      <li class="group-title">Diet/Lifestyle</li>
      <li class="condition"><span class="condition-name">Drink more than one glass alcohol per day</span><span class="answer"><span>Yes</span><i class="tick-box"></i><span>No</span><i class="tick-box"></i></span></li>
      <li class="condition"><span class="condition-name">Smoking</span><span class="answer"><span>Yes</span><i class="tick-box"></i><span>No</span><i class="tick-box"></i></span></li>
      <li class="condition"><span class="condition-name">Carbonated drinks</span><span class="answer"><span>Yes</span><i class="tick-box"></i><span>No</span><i class="tick-box"></i></span></li>
      <li class="condition"><span class="condition-name">Sugary foods</span><span class="answer"><span>Yes</span><i class="tick-box"></i><span>No</span><i class="tick-box"></i></span></li>
      <li class="group-title">Blood</li>
      <li class="condition"><span class="condition-name">Anaemia</span><span class="answer"><span>Yes</span><i class="tick-box"></i><span>No</span><i class="tick-box"></i></span></li>
      <li class="condition"><span class="condition-name">Blood Clots</span><span class="answer"><span>Yes</span><i class="tick-box"></i><span>No</span><i class="tick-box"></i></span></li>
      <li class="condition"><span class="condition-name">Leukemia</span><span class="answer"><span>Yes</span><i class="tick-box"></i><span>No</span><i class="tick-box"></i></span></li>
      <li class="condition"><span class="condition-name">Low platelets</span><span class="answer"><span>Yes</span><i class="tick-box"></i><span>No</span><i class="tick-box"></i></span></li>
      <li class="condition"><span class="condition-name">Lymphoma</span><span class="answer"><span>Yes</span><i class="tick-box"></i><span>No</span><i class="tick-box"></i></span></li>
      <li class="condition"><span class="condition-name">Haemophilia</span><span class="answer"><span>Yes</span><i class="tick-box"></i><span>No</span><i class="tick-box"></i></span></li>
      <li class="group-title">Chest</li>
      <li class="condition"><span class="condition-name">Bronchitis</span><span class="answer"><span>Yes</span><i class="tick-box"></i><span>No</span><i class="tick-box"></i></span></li>
      <li class="condition"><span class="condition-name">Cystic Fibrosis</span><span class="answer"><span>Yes</span><i class="tick-box"></i><span>No</span><i class="tick-box"></i></span></li>
      <li class="condition"><span class="condition-name">Emphysema</span><span class="answer"><span>Yes</span><i class="tick-box"></i><span>No</span><i class="tick-box"></i></span></li>
      <li class="condition"><span class="condition-name">Pneumonia</span><span class="answer"><span>Yes</span><i class="tick-box"></i><span>No</span><i class="tick-box"></i></span></li>
      <li class="group-title">Infectious Disease</li>
      <li class="condition"><span class="condition-name">Creutzfeldt-Jakob Disease</span><span class="answer"><span>Yes</span><i class="tick-box"></i><span>No</span><i class="tick-box"></i></span></li>
      <li class="condition"><span class="condition-name">Hepatitis A,B,C,D</span><span class="answer"><span>Yes</span><i class="tick-box"></i><span>No</span><i class="tick-box"></i></span></li>
    </ul>
    <ul class="condition-list">
      <li class="condition"><span class="condition-name">HIV/AIDS</span><span class="answer"><span>Yes</span><i class="tick-box"></i><span>No</span><i class="tick-box"></i></span></li>
      <li class="condition"><span class="condition-name">Influenza</span><span class="answer"><span>Yes</span><i class="tick-box"></i><span>No</span><i class="tick-box"></i></span></li>
      <li class="condition"><span class="condition-name">Shingles</span><span class="answer"><span>Yes</span><i class="tick-box"></i><span>No</span><i class="tick-box"></i></span></li>
      <li class="condition"><span class="condition-name">Tuberculosis</span><span class="answer"><span>Yes</span><i class="tick-box"></i><span>No</span><i class="tick-box"></i></span></li>
      <li class="group-title">Heart</li>
      <li class="condition"><span class="condition-name">Angina</span><span class="answer"><span>Yes</span><i class="tick-box"></i><span>No</span><i class="tick-box"></i></span></li>
      <li class="condition"><span class="condition-name">Atrial Fibrillation</span><span class="answer"><span>Yes</span><i class="tick-box"></i><span>No</span><i class="tick-box"></i></span></li>
      <li class="condition"><span class="condition-name">Blood Pressure (High/Low)</span><span class="answer"><span>Yes</span><i class="tick-box"></i><span>No</span><i class="tick-box"></i></span></li>
      <li class="condition"><span class="condition-name">Congenital Heart Disease</span><span class="answer"><span>Yes</span><i class="tick-box"></i><span>No</span><i class="tick-box"></i></span></li>
      <li class="condition"><span class="condition-name">Heart attack</span><span class="answer"><span>Yes</span><i class="tick-box"></i><span>No</span><i class="tick-box"></i></span></li>
      <li class="condition"><span class="condition-name">Heart murmur</span><span class="answer"><span>Yes</span><i class="tick-box"></i><span>No</span><i class="tick-box"></i></span></li>
      <li class="condition"><span class="condition-name">Heart surgery</span><span class="answer"><span>Yes</span><i class="tick-box"></i><span>No</span><i class="tick-box"></i></span></li>
      <li class="condition"><span class="condition-name">Heart valve replacement</span><span class="answer"><span>Yes</span><i class="tick-box"></i><span>No</span><i class="tick-box"></i></span></li>
      <li class="condition"><span class="condition-name">Infective endocarditis</span><span class="answer"><span>Yes</span><i class="tick-box"></i><span>No</span><i class="tick-box"></i></span></li>
      <li class="condition"><span class="condition-name">Rheumatic Heart Disease</span><span class="answer"><span>Yes</span><i class="tick-box"></i><span>No</span><i class="tick-box"></i></span></li>
      <li class="condition"><span class="condition-name">Pacemaker</span><span class="answer"><span>Yes</span><i class="tick-box"></i><span>No</span><i class="tick-box"></i></span></li>
      <li class="condition"><span class="condition-name">Stent</span><span class="answer"><span>Yes</span><i class="tick-box"></i><span>No</span><i class="tick-box"></i></span></li>
      <li class="group-title">Other</li>
      <li class="condition"><span class="condition-name">Anxiety/PTSD</span><span class="answer"><span>Yes</span><i class="tick-box"></i><span>No</span><i class="tick-box"></i></span></li>
      <li class="condition"><span class="condition-name">Arthritis</span><span class="answer"><span>Yes</span><i class="tick-box"></i><span>No</span><i class="tick-box"></i></span></li>
      <li class="condition"><span class="condition-name">Alzheimer’s</span><span class="answer"><span>Yes</span><i class="tick-box"></i><span>No</span><i class="tick-box"></i></span></li>
      <li class="condition"><span class="condition-name">Asthma</span><span class="answer"><span>Yes</span><i class="tick-box"></i><span>No</span><i class="tick-box"></i></span></li>
      <li class="condition"><span class="condition-name">Anaphylaxis</span><span class="answer"><span>Yes</span><i class="tick-box"></i><span>No</span><i class="tick-box"></i></span></li>
      <li class="condition"><span class="condition-name">Auto-immune disease</span><span class="answer"><span>Yes</span><i class="tick-box"></i><span>No</span><i class="tick-box"></i></span></li>
      <li class="condition"><span class="condition-name">Coeliac</span><span class="answer"><span>Yes</span><i class="tick-box"></i><span>No</span><i class="tick-box"></i></span></li>
      <li class="condition"><span class="condition-name">Depression</span><span class="answer"><span>Yes</span><i class="tick-box"></i><span>No</span><i class="tick-box"></i></span></li>
      <li class="condition"><span class="condition-name">Diabetes</span><span class="answer"><span>Yes</span><i class="tick-box"></i><span>No</span><i class="tick-box"></i></span></li>
      <li class="condition"><span class="condition-name">Epilepsy</span><span class="answer"><span>Yes</span><i class="tick-box"></i><span>No</span><i class="tick-box"></i></span></li>
      <li class="condition"><span class="condition-name">Kidney Disease</span><span class="answer"><span>Yes</span><i class="tick-box"></i><span>No</span><i class="tick-box"></i></span></li>
      <li class="condition"><span class="condition-name">Liver Disease</span><span class="answer"><span>Yes</span><i class="tick-box"></i><span>No</span><i class="tick-box"></i></span></li>
      <li class="condition"><span class="condition-name">Osteoporosis</span><span class="answer"><span>Yes</span><i class="tick-box"></i><span>No</span><i class="tick-box"></i></span></li>
      <li class="condition"><span class="condition-name">Parkinson’s</span><span class="answer"><span>Yes</span><i class="tick-box"></i><span>No</span><i class="tick-box"></i></span></li>
      <li class="condition"><span class="condition-name">Radiation to Head/Neck</span><span class="answer"><span>Yes</span><i class="tick-box"></i><span>No</span><i class="tick-box"></i></span></li>
      <li class="condition"><span class="condition-name">Schizophrenia</span><span class="answer"><span>Yes</span><i class="tick-box"></i><span>No</span><i class="tick-box"></i></span></li>
      <li class="condition"><span class="condition-name">Snoring</span><span class="answer"><span>Yes</span><i class="tick-box"></i><span>No</span><i class="tick-box"></i></span></li>
      <li class="condition"><span class="condition-name">Sleep apnea</span><span class="answer"><span>Yes</span><i class="tick-box"></i><span>No</span><i class="tick-box"></i></span></li>
      <li class="condition"><span class="condition-name">Stroke</span><span class="answer"><span>Yes</span><i class="tick-box"></i><span>No</span><i class="tick-box"></i></span></li>
    </ul>
  </div>
  <footer class="sign-off">
    <div class="sign-lines">
      <div class="sign-field date">Date <span class="sign-line"></span></div>
      <div class="sign-field signature">Signature <span class="sign-line"></span></div>
    </div>
    <p class="thanks">Thank you for the time to complete your medical history form.<br>
    Oral health is linked to overall health and this comprehensive questionnaire will help us to provide you with optimal and safe care.</p>
  </footer>
</main>
</body>
</html>
```